A5 Magazine Cover Design

I need a front cover designing for a new community magazine called ORLEEN. ORLEEN will be listing local buisnesses and local interest articles for the residents in my area. I need the look to be clean but inviting.

I will consider any colour combination as long as its not too bright.

```html
<!DOCTYPE html>
<html lang="en">
<head>
<meta charset="utf-8">
<title>ORLEEN — Community Magazine Cover</title>
<link rel="stylesheet" href="https://fonts.googleapis.com/css2?family=Open+Sans:wght@700;800&display=swap">
<style>
  :root {
    --teal: #1a9f7a;
    --band: #ecf2f0;
    --glow: #3ee8bf;
    --white: #ffffff;
  }
  html, body {
    margin: 0;
    padding: 0;
    width: 846px;
    height: 1200px;
    overflow: hidden;
    background: var(--teal);
  }
  .cover {
    position: relative;
    width: 846px;
    height: 1200px;
    background: var(--teal);
    overflow: hidden;
  }
  .cover-art {
    position: absolute;
    inset: 0;
    width: 846px;
    height: 1200px;
    display: block;
  }
  .masthead-title {
    font-family: "Open Sans", Arial, sans-serif;
    font-weight: 800;
    font-size: 222px;
    fill: var(--teal);
  }
  .masthead-tagline {
    font-family: "Open Sans", Arial, sans-serif;
    font-weight: 700;
    font-size: 30px;
    fill: var(--white);
  }
  .rail, .band { fill: var(--band); }
</style>
</head>
<body>
<main class="cover">
  <svg class="cover-art" viewBox="0 0 846 1200" xmlns="http://www.w3.org/2000/svg">
    <defs>
      <radialGradient id="glow-left" cx="50%" cy="50%" r="50%">
        <stop offset="0" stop-color="#3ee8bf" stop-opacity="0.7"/>
        <stop offset="1" stop-color="#3ee8bf" stop-opacity="0"/>
      </radialGradient>
      <radialGradient id="glow-right" cx="50%" cy="50%" r="50%">
        <stop offset="0" stop-color="#ffffff" stop-opacity="0.3"/>
        <stop offset="1" stop-color="#ffffff" stop-opacity="0"/>
      </radialGradient>
    </defs>

    <g class="light-streaks" role="img" aria-label="Soft light streaks glowing around the masthead band">
      <ellipse cx="20" cy="555" rx="230" ry="130" fill="url(#glow-left)"/>
      <ellipse cx="170" cy="270" rx="220" ry="100" fill="url(#glow-left)" opacity="0.3"/>
      <ellipse cx="810" cy="170" rx="170" ry="120" fill="url(#glow-right)"/>
      <ellipse cx="790" cy="500" rx="160" ry="120" fill="url(#glow-right)"/>
    </g>

    <rect class="rail rail-inner" x="779" y="-10" width="15" height="1042" rx="4"/>
    <rect class="rail rail-outer" x="806" y="300" width="19" height="920"/>

    <rect class="band" x="-60" y="330" width="1000" height="213" transform="rotate(-8.5 0 330)"/>

    <text class="masthead-title" x="55" y="508" textLength="748" lengthAdjust="spacingAndGlyphs" transform="rotate(-8.5 55 508)">ORLEEN</text>
    <text class="masthead-tagline" x="121" y="558" textLength="648" lengthAdjust="spacingAndGlyphs" transform="rotate(-8.5 121 558)">searches , reviews and recommends locally</text>
  </svg>
</main>
</body>
</html>
```